Local fast-growing company in the service sector

We are looking for a modern business card design, which should also appear on our letterheads

Target Market(s)

Private and industrial sectors

Contact Information for Business Card

Vorname Name
Kellberger Str. 18
72451 Feldbrunn
Tel.: 07146-839214-0
Name@agentur-kvtl.de

Colors
9d9d9d
919191
aaaaaa

Requirements
Must have
• The logo (file) in silver

```html
<!DOCTYPE html>
<html lang="de">
<head>
<meta charset="utf-8">
<title>KVTL Visitenkarte</title>
<link href="https://fonts.googleapis.com/css2?family=Open+Sans:wght@400;600;700&display=swap" rel="stylesheet">
<style>
  :root {
    --stage: #000000;
    --card: #ffffff;
    --brand-silver: #9d9d9d;
    --text-dark: #3a3a3a;
    --text-body: #222222;
    --rule: #6f6f6f;
    --icon: #8a8a8a;
  }
  html, body {
    margin: 0;
    width: 1200px;
    height: 900px;
    overflow: hidden;
    background: var(--stage);
    font-family: "Open Sans", Arial, sans-serif;
  }
  .canvas { position: relative; width: 1200px; height: 900px; }
  .card {
    position: absolute;
    width: 477px;
    height: 293px;
    background: var(--card);
    overflow: hidden;
  }
  .card--front { left: 116px; top: 275px; border-radius: 0 56px 0 56px; }
  .card--back  { left: 622px; top: 276px; height: 292px; border-radius: 56px 0 56px 0; }

  .brand-name {
    position: absolute;
    margin: 0;
    font-weight: 700;
    color: var(--brand-silver);
    letter-spacing: 2px;
    line-height: 1;
  }
  .card--front .brand-name { left: 272px; top: 56px; font-size: 52px; }
  .brand-mark {
    position: absolute;
    left: 222px; top: 62px;
    width: 38px; height: 38px;
    background: var(--brand-silver);
  }
  .card--back .brand-name { left: 196px; top: 174px; font-size: 72px; letter-spacing: 4px; }

  .holder {
    position: absolute;
    left: 19px; top: 150px;
    margin: 0;
    font-size: 17px;
    font-weight: 600;
    color: var(--text-dark);
  }
  .divider {
    position: absolute;
    left: 0; right: 0; top: 183px;
    height: 2px;
    background: var(--rule);
  }
  .contact {
    position: absolute;
    right: 25px; top: 197px;
    margin: 0; padding: 0;
    list-style: none;
    text-align: right;
    font-size: 12.5px;
    color: var(--text-body);
  }
  .contact li { display: flex; justify-content: flex-end; align-items: center; height: 17.5px; gap: 6px; }
  .contact svg { width: 10px; height: 10px; fill: var(--icon); }
  .address {
    position: absolute;
    right: 25px; top: 256px;
    margin: 0;
    font-size: 12.5px;
    font-style: normal;
    color: var(--text-body);
  }
</style>
</head>
<body>
<main class="canvas">
  <section class="card card--front">
    <span class="brand-mark"></span>
    <p class="brand-name">KVTL</p>
    <p class="holder">Vorname Name</p>
    <div class="divider"></div>
    <ul class="contact">
      <li>07146-839214-0
        <svg viewBox="0 0 10 10"><path d="M2 0.5l1.6 1.9-.9 1.2c.6 1.3 1.5 2.2 2.8 2.8l1.2-.9 1.9 1.6-1 1.4C4.6 8.4 1.6 5.4 0.5 1.5z"/></svg>
      </li>
      <li>Name@agentur-kvtl.de
        <svg viewBox="0 0 10 10"><path d="M0.5 2h9v6h-9z" fill="var(--icon)"/><path d="M1 2.6l4 2.9 4-2.9" stroke="#fff" stroke-width="0.8" fill="none"/></svg>
      </li>
      <li>www.agentur-kvtl.de
        <svg viewBox="0 0 10 10"><circle cx="5" cy="5" r="4.5"/><path d="M5 .5v9M.5 5h9M5 .5c-2 2.5-2 6.5 0 9M5 .5c2 2.5 2 6.5 0 9" stroke="#fff" stroke-width="0.6" fill="none"/></svg>
      </li>
    </ul>
    <address class="address">Kellberger Str. 18 72451 Feldbrunn</address>
  </section>

  <section class="card card--back">
    <p class="brand-name">KVTL</p>
  </section>
</main>
</body>
</html>
```